Design a Travel and Tourism website

We would like a freelancer to design a website that is essentially easy to use and navigate database providing local information for Travelers about destination countries.

We proposed website would discuss different rates, fees, visa requirement, resort locations, cheap flights, etc. This website should be elegant and modern. Our business name is rovanix.
Some reference websites are zemplorift.ca, brindlefoxhaven.com,
There should be a forum in the website where travell\ers discuss about their first hand tranvel experience to such destinations.

Tourism

```html
<!DOCTYPE html>
<html lang="en">
<head>
<meta charset="utf-8">
<title>rovanix — Travel and Tourism</title>
<link rel="stylesheet" href="https://fonts.googleapis.com/css2?family=Nunito+Sans:wght@300;400;600;700&family=Open+Sans:wght@400;600&display=swap">
<style>
:root{
  --blue:#1aa3e0;
  --blue-dark:#0f86bf;
  --footer:#1ba8e6;
  --orange:#f39200;
  --orange-dark:#e27d00;
  --ink:#222;
  --muted:#8a8a8a;
  --soft:#eeeeee;
  --white:#fff;
  --price:#f08a00;
  --star:#f5a400;
  --placeholder-a:#dfe9f1;
  --placeholder-b:#eef1f3;
}
*{box-sizing:border-box;margin:0;padding:0}
html,body{width:1200px;height:2510px;overflow:hidden}
body{position:relative;background:var(--white);font-family:"Nunito Sans",sans-serif;color:var(--ink)}

/* header */
.site-header{position:absolute;left:0;top:0;width:1200px;height:90px;background:var(--white)}
.brand{position:absolute;left:125px;top:14px;font-size:46px;font-weight:400;color:var(--blue);letter-spacing:.5px;line-height:1}
.main-nav a{position:absolute;top:33px;font-size:17px;color:#666;text-decoration:none;font-family:"Open Sans",sans-serif}
.nav-icon{position:absolute;top:28px}

/* hero */
.hero-photo{position:absolute;left:0;top:90px;width:1200px;height:529px;
  background:linear-gradient(180deg,#d9c79a 0%,#e8c77e 22%,#b9a48a 45%,#6f7d86 62%,#8c8a80 78%,#5f5a52 100%)}
.search-tabs .tab{position:absolute;top:300px;height:43px;width:147px;background:var(--white);color:var(--orange);font-size:20px;text-align:center;line-height:43px;text-transform:uppercase}
.search-tabs .tab.is-active{background:var(--orange-dark);color:var(--white)}
.search-panel{position:absolute;left:127px;top:343px;width:946px;height:111px;background:rgba(243,146,0,.93)}
.field-label{position:absolute;top:362px;font-size:16px;color:var(--white)}
.field{position:absolute;top:388px;height:39px;background:var(--white);font-family:"Open Sans",sans-serif;font-size:13px;color:#999;line-height:39px;padding-left:34px;white-space:nowrap;overflow:hidden}
.field svg{position:absolute;left:11px;top:12px}
.btn-search{position:absolute;left:937px;top:388px;width:116px;height:39px;background:#1b1b1b;color:var(--white);font-size:18px;text-align:center;line-height:39px}
.slider-dot{position:absolute;top:582px;width:14px;height:14px;border-radius:50%;background:#222}
.slider-dot.is-current{background:transparent;border:2px solid #222}

/* welcome */
.welcome-title{position:absolute;left:126px;top:693px;font-size:38px;font-weight:400;color:#1d1d1d}
.welcome-text{position:absolute;left:127px;top:760px;width:490px;font-family:"Open Sans",sans-serif;font-size:14.5px;line-height:28px;color:var(--muted)}
.btn-read{position:absolute;left:127px;top:889px;width:133px;height:38px;background:var(--blue);color:var(--white);font-size:16px;text-align:center;line-height:38px}
.welcome-visual{position:absolute;left:640px;top:645px;width:365px;height:360px;
  background:linear-gradient(160deg,var(--placeholder-a) 0%,var(--placeholder-b) 100%)}

/* destinations */
.destinations{position:absolute;left:0;top:1013px;width:1200px;height:487px;background:var(--soft)}
.section-title{position:absolute;font-size:30px;font-weight:400;color:var(--blue)}
.dest-card{position:absolute;top:1135px;width:303px;height:311px;background:var(--white);box-shadow:0 1px 4px rgba(0,0,0,.18)}
.dest-photo{position:absolute;left:0;top:0;width:303px;height:184px}
.dest-card .notch{position:absolute;left:131px;top:170px;width:0;height:0;border-left:14px solid transparent;border-right:14px solid transparent;border-bottom:14px solid var(--white)}
.dest-name{position:absolute;left:23px;top:210px;font-size:18px;font-weight:400;color:#333}
.dest-sub{position:absolute;left:23px;top:240px;font-family:"Open Sans",sans-serif;font-size:11.5px;color:#888}
.price-old{position:absolute;left:27px;top:266px;font-size:19px;color:#444;text-decoration:line-through}
.price-new{position:absolute;left:78px;top:259px;font-size:27px;color:var(--price)}
.rating{position:absolute;left:210px;top:268px}

/* categories */
.category-strip{position:absolute;left:131px;top:1547px;width:952px;height:217px}
.category{position:absolute;top:0;width:237px;height:217px}
.category-label{position:absolute;left:0;top:128px;width:100%;text-align:center;font-size:19px;font-weight:600;color:var(--white);text-transform:uppercase}
.category svg{position:absolute;left:88px;top:52px}
.strip-arrow{position:absolute;top:1627px}

/* info links */
.info-col{position:absolute;top:1902px;list-style:none;font-family:"Open Sans",sans-serif;font-size:14.5px;color:var(--muted)}
.info-col li{height:38.5px;padding-left:17px;position:relative}
.info-col li::before{content:"";position:absolute;left:0;top:6px;border-left:6px solid #aaa;border-top:5px solid transparent;border-bottom:5px solid transparent}

/* footer */
.site-footer{position:absolute;left:0;top:2143px;width:1200px;height:367px;background:var(--footer);color:var(--white)}
.footer-col{position:absolute;top:50px}
.footer-col h4{font-size:18px;font-weight:700;margin-bottom:9px;text-transform:uppercase}
.footer-col ul{list-style:none;font-size:15px;line-height:26px}
.newsletter-input{position:absolute;left:867px;top:90px;width:224px;height:35px;background:var(--white);font-family:"Open Sans",sans-serif;font-size:13px;color:#bbb;line-height:35px;padding-left:33px}
.newsletter-input svg{position:absolute;left:11px;top:12px}
.btn-subscribe{position:absolute;left:867px;top:134px;width:111px;height:35px;background:var(--blue-dark);font-size:15px;font-weight:600;text-align:center;line-height:35px}
.social{position:absolute;top:189px;width:36px;height:36px;border-radius:50%;background:var(--white)}
.footer-rule{position:absolute;left:142px;top:298px;width:938px;height:1px;background:rgba(255,255,255,.6)}
.copyright{position:absolute;left:0;top:323px;width:1218px;text-align:center;font-family:"Open Sans",sans-serif;font-size:13px}
</style>
</head>
<body>

<header class="site-header">
  <div class="brand">rovanix</div>
  <nav class="main-nav">
    <a style="left:490px">About</a>
    <a style="left:571px">Flights</a>
    <a style="left:654px">Hotel</a>
    <a style="left:728px">Visa</a>
    <a style="left:792px">Tours</a>
    <a style="left:867px">Support</a>
  </nav>
  <svg class="nav-icon" style="left:966px" width="24" height="26" viewBox="0 0 24 26"><circle cx="12" cy="7" r="6" fill="#1aa3e0"/><path d="M1 26c0-8 5-11 11-11s11 3 11 11z" fill="#1aa3e0"/></svg>
  <svg class="nav-icon" style="left:1016px" width="26" height="26" viewBox="0 0 26 26"><path d="M14 2h9v22h-9v-3h6V5h-6z" fill="#1aa3e0"/><path d="M2 10h8V5l8 8-8 8v-5H2z" fill="#1aa3e0"/></svg>
</header>

<section class="hero">
  <div class="hero-photo" role="img" aria-label="Photo of a family running and jumping along the shore at sunset"></div>
  <div class="search-tabs">
    <div class="tab is-active" style="left:127px;width:149px">Holiday</div>
    <div class="tab" style="left:281px">Flights</div>
    <div class="tab" style="left:434px">Hotels</div>
    <div class="tab" style="left:588px;width:150px">Other</div>
  </div>
  <div class="search-panel"></div>
  <div class="field-label" style="left:156px">Find Tour</div>
  <div class="field-label" style="left:412px">Location</div>
  <div class="field-label" style="left:645px">Depart</div>
  <div class="field-label" style="left:794px">Arrival</div>
  <div class="field" style="left:156px;width:247px"><svg width="15" height="15" viewBox="0 0 15 15"><circle cx="6" cy="6" r="4.5" fill="none" stroke="#999" stroke-width="2"/><path d="M9.5 9.5l4 4" stroke="#999" stroke-width="2"/></svg>Tour Tittle here</div>
  <div class="field" style="left:412px;width:221px"><svg width="12" height="16" viewBox="0 0 12 16"><path d="M6 0a6 6 0 0 1 6 6c0 4-6 10-6 10S0 10 0 6a6 6 0 0 1 6-6z" fill="#999"/><circle cx="6" cy="6" r="2" fill="#fff"/></svg>City Destnation</div>
  <div class="field" style="left:639px;width:141px;padding-left:48px"><svg width="16" height="16" viewBox="0 0 16 16"><rect x="1" y="2" width="14" height="13" fill="none" stroke="#999" stroke-width="1.5"/><path d="M1 6h14M5 9h2M9 9h2M5 12h2M9 12h2" stroke="#999" stroke-width="1.5"/></svg>02/11/17</div>
  <div class="field" style="left:788px;width:141px;padding-left:48px"><svg width="16" height="16" viewBox="0 0 16 16"><rect x="1" y="2" width="14" height="13" fill="none" stroke="#999" stroke-width="1.5"/><path d="M1 6h14M5 9h2M9 9h2M5 12h2M9 12h2" stroke="#999" stroke-width="1.5"/></svg>10/11/17</div>
  <div class="btn-search">Search</div>
  <span class="slider-dot is-current" style="left:554px"></span>
  <span class="slider-dot" style="left:577px"></span>
  <span class="slider-dot" style="left:601px"></span>
  <span class="slider-dot" style="left:623px"></span>
</section>

<section class="welcome">
  <h1 class="welcome-title">Welcome to Our Website</h1>
  <p class="welcome-text">Praesent elementum elit at tellus nec ultricies sit amet porttitor mattis enim In massa libero interdum nec interdum vel blandit sed nulla In ullamcorper est eget tempor cursus neque mi consectetuer mi a ultricies massa est sed nisl Class aptent taciti sociosqu ad litora to</p>
  <div class="btn-read">Read More</div>
  <div class="welcome-visual" role="img" aria-label="Illustration of an open red suitcase holding a tiny beach with palm trees, umbrella and loungers"></div>
</section>

<section class="destinations">
  <h2 class="section-title" style="left:130px;top:63px">Top Destinations</h2>
</section>
<article class="dest-card" style="left:129px">
  <div class="dest-photo" role="img" aria-label="Photo of a thatched beach umbrella and loungers on white sand" style="background:linear-gradient(180deg,#3f8ed6 0%,#8cc6ea 45%,#e6d8bd 70%,#cdb690 100%)"></div>
  <span class="notch"></span>
  <h3 class="dest-name">Tour Tittle here</h3>
  <p class="dest-sub">per inceptos hymenaeos Proin nulla arcu</p>
  <span class="price-old">$229</span><span class="price-new">$175</span>
  <svg class="rating" width="72" height="16" viewBox="0 0 72 16"><g fill="#f5a400"><path id="st" d="M8 0l2.4 5 5.6.6-4.2 3.8 1.2 5.6L8 12.2 3 15l1.2-5.6L0 5.6 5.6 5z"/><use href="#st" x="18"/><use href="#st" x="36"/><use href="#st" x="54"/></g></svg>
</article>
<article class="dest-card" style="left:445px">
  <div class="dest-photo" role="img" aria-label="Photo of a stone bridge over a calm river with a town behind" style="background:linear-gradient(180deg,#bfc9d6 0%,#a9b8a0 35%,#6f8f4e 55%,#7d9a86 75%,#5e7a66 100%)"></div>
  <span class="notch"></span>
  <h3 class="dest-name">Tour Tittle here</h3>
  <p class="dest-sub">per inceptos hymenaeos Proin nulla arcu</p>
  <span class="price-old">$229</span><span class="price-new">$175</span>
  <svg class="rating" width="72" height="16" viewBox="0 0 72 16"><g fill="#f5a400"><use href="#st"/><use href="#st" x="18"/><use href="#st" x="36"/><use href="#st" x="54"/></g></svg>
</article>
<article class="dest-card" style="left:763px">
  <div class="dest-photo" role="img" aria-label="Photo of a resort pool lined with palm trees and parasols" style="background:linear-gradient(180deg,#4f8a4a 0%,#7aa86a 35%,#c9b89a 55%,#2fb0d8 70%,#1684b8 100%)"></div>
  <span class="notch"></span>
  <h3 class="dest-name">Tour Tittle here</h3>
  <p class="dest-sub">per inceptos hymenaeos Proin nulla arcu</p>
  <span class="price-old">$229</span><span class="price-new">$175</span>
  <svg class="rating" width="72" height="16" viewBox="0 0 72 16"><g fill="#f5a400"><use href="#st"/><use href="#st" x="18"/><use href="#st" x="36"/><use href="#st" x="54"/></g></svg>
</article>

<svg class="strip-arrow" style="left:88px" width="24" height="60" viewBox="0 0 24 60"><path d="M22 2L2 30l20 28" fill="none" stroke="#555" stroke-width="2"/></svg>
<div class="category-strip">
  <div class="category" style="left:0;background:linear-gradient(135deg,#6b8fa8,#c7b9a0 50%,#8fa4b2)" role="img" aria-label="Photo of a family with hats on a beach">
    <svg width="60" height="60" viewBox="0 0 60 60"><path d="M6 26a24 20 0 0 1 48 0z" fill="none" stroke="#fff" stroke-width="4"/><path d="M30 6v20M18 26l12-20 12 20" fill="none" stroke="#fff" stroke-width="3"/><path d="M30 26l10 30M10 46h40M16 46l-4 10M44 46l4 10" stroke="#fff" stroke-width="4"/></svg>
    <div class="category-label">Latest Tours</div>
  </div>
  <div class="category" style="left:238px;background:linear-gradient(180deg,#4b6d55,#3f8aa6 60%,#1e6f9a)" role="img" aria-label="Photo of a resort pool with palm trees">
    <svg width="60" height="60" viewBox="0 0 60 60"><path d="M30 22c-2 12-6 26-10 36h8c3-10 5-24 4-36z" fill="#fff"/><path d="M31 22C24 8 12 8 6 16c8-4 16-2 25 6zM31 22C38 6 52 8 56 16c-8-4-16-1-25 6zM31 22c-4-10 0-18 6-20-3 6-4 12-6 20z" fill="#fff"/></svg>
    <div class="category-label">Top Resorts</div>
  </div>
  <div class="category" style="left:476px;background:linear-gradient(180deg,#1f4f86,#3c79b5 60%,#6c9fcd)" role="img" aria-label="Photo of a blue evening sky">
    <svg width="60" height="60" viewBox="0 0 60 60"><path d="M52 4c4-2 6 0 4 4L44 20l6 30-5 4-12-22-10 10 1 10-4 3-5-12-12-5 3-4 10 1 10-10L4 23l4-5 30 6z" fill="#fff"/></svg>
    <div class="category-label">Cheap Flights</div>
  </div>
  <div class="category" style="left:714px;background:linear-gradient(135deg,#4a4038,#7b6a55 50%,#3a4450)" role="img" aria-label="Photo of travel documents and passports on a desk">
    <svg width="60" height="60" viewBox="0 0 60 60"><rect x="4" y="14" width="52" height="34" fill="none" stroke="#fff" stroke-width="3"/><path d="M4 22h52M12 34h24M12 40h14" stroke="#fff" stroke-width="3"/></svg>
    <div class="category-label">Visa &amp; Other</div>
  </div>
</div>
<svg class="strip-arrow" style="left:1098px" width="24" height="60" viewBox="0 0 24 60"><path d="M2 2l20 28L2 58" fill="none" stroke="#555" stroke-width="2"/></svg>

<section class="more-info">
  <h2 class="section-title" style="left:137px;top:1840px;font-size:25px">Check Out More Information</h2>
  <ul class="info-col" style="left:139px"><li>Praesent elementum</li><li>Elit at tellus nec ultricies</li><li>Porttitor mattis enim</li><li>Massa libero interdum</li></ul>
  <ul class="info-col" style="left:417px"><li>Donec dictum lectus</li><li>Non odio</li><li>Cras a ante</li><li>Vitae enim iaculis</li></ul>
  <ul class="info-col" style="left:639px"><li>Dignissim congue leo</li><li>Elit at tellus nec</li><li>Porttitor mattis enim</li><li>Massa libero int</li></ul>
  <ul class="info-col" style="left:902px"><li>Duis quam Nam</li><li>Eget lacus</li><li>Aliquam erat</li><li>Volutpat Quisque</li></ul>
</section>

<footer class="site-footer">
  <div class="footer-col" style="left:131px"><h4>Quick Links</h4><ul><li>About Us</li><li>Our Tours</li><li>Gallery</li><li>Reviews</li><li>Term of Use</li></ul></div>
  <div class="footer-col" style="left:316px"><h4>Tours &amp; Hotel</h4><ul><li>Kumarakom Hotels</li><li>Lucknow Hotels</li><li>Ludhiana Hotels</li><li>Maharashtra Hotels</li><li>Mumbai Hotels</li></ul></div>
  <div class="footer-col" style="left:534px"><h4>Resources</h4><ul><li>Privacy Policy</li><li>FAQ</li><li>Contact Us</li><li>Newsletters</li></ul></div>
  <div class="footer-col" style="left:720px"><h4>Support</h4><ul><li>Support</li><li>Career</li><li>Advertise</li><li>Blogs</li></ul></div>
  <div class="footer-col" style="left:867px"><h4>Join Newsletters</h4></div>
  <div class="newsletter-input"><svg width="14" height="11" viewBox="0 0 14 11"><rect width="14" height="11" fill="#bbb"/><path d="M0 0l7 6 7-6" fill="none" stroke="#fff" stroke-width="1.3"/></svg>Email address</div>
  <div class="btn-subscribe">Subscribe</div>
  <span class="social" style="left:867px"></span>
  <span class="social" style="left:914px"></span>
  <span class="social" style="left:960px"></span>
  <span class="social" style="left:1006px"></span>
  <div class="footer-rule"></div>
  <p class="copyright">© 2017 Company Name&nbsp; All right reserved</p>
</footer>

</body>
</html>
```